Small Business Broker Business Card Design

A business card design for a small business brokerage, which is a financial service, not unlike real estate brokerage, but for small businesses such as laundromats, pizza shops, restaurants, cleaners etc. The designs should all be simple, more conservative in nature, using the colors and font of the logo. Again, think real estate Brokerage as a business context
Contact Information for Business Card
Name: Glen R. Harlow. Title: Small Business Advisor. Email: g.harlow@bayfieldcapitalworks.example. Mobile: (555) 274-3918. Office: (555) 806-2147. www.bayfieldcapitalworks.example

```html
<!DOCTYPE html>
<html lang="en">
<head>
<meta charset="utf-8">
<title>Bayfield Capital Works — Business Card</title>
<link rel="stylesheet" href="https://fonts.googleapis.com/css2?family=League+Spartan:wght@600;700&family=Montserrat:wght@400;500&display=swap">
<style>
  :root {
    --navy: #1b3969;
    --green: #8dc63f;
    --white: #ffffff;
    --ink: #1d1d1f;
    --stage: #e9e9ea;
  }
  * { margin: 0; padding: 0; box-sizing: border-box; }
  html, body { width: 1093px; height: 1200px; overflow: hidden; }
  body { background: var(--stage); font-family: "Montserrat", Arial, sans-serif; position: relative; }

  .card {
    position: absolute;
    left: 265px;
    width: 581px;
    height: 364px;
    border-radius: 18px;
    overflow: hidden;
  }
  .card--front { top: 225px; background: var(--white); }
  .card--back  { top: 615px; background: var(--navy); }

  .brand-block {
    position: absolute;
    display: flex;
    align-items: center;
    gap: 10px;
    font-family: "League Spartan", Arial, sans-serif;
    font-weight: 700;
    line-height: 1.02;
    letter-spacing: 0.5px;
  }
  .brand-block__square { width: 18px; height: 18px; flex: none; background: var(--green); }
  .card--front .brand-block { left: 49px; top: 118px; width: 190px; font-size: 27px; color: var(--navy); }
  .card--back .brand-block { left: 0; right: 0; top: 110px; justify-content: center; font-size: 30px; color: var(--white); }

  .divider {
    position: absolute;
    left: 257px; top: 74px;
    width: 1.5px; height: 163px;
    background: var(--navy);
  }

  .person { position: absolute; left: 271px; top: 72px; }
  .person__name {
    font-family: "League Spartan", Arial, sans-serif;
    font-weight: 700; font-size: 23px; color: var(--navy); line-height: 1.1;
  }
  .person__title { font-size: 12.5px; color: var(--ink); margin-top: 1px; }

  .contacts { position: absolute; left: 280px; top: 158px; list-style: none; }
  .contacts li {
    display: flex; align-items: center; gap: 9px;
    font-size: 12.6px; color: var(--ink); height: 19.5px;
  }
  .contacts li:nth-child(2) { margin-top: 5px; }
  .contacts svg { width: 12px; height: 12px; fill: var(--navy); flex: none; }

  .wordmark {
    position: absolute; left: 0; right: 0; text-align: center;
    font-family: "League Spartan", Arial, sans-serif;
  }
  .wordmark__name { font-weight: 700; font-size: 28px; letter-spacing: 0.6px; line-height: 1; }
  .wordmark__tagline { font-weight: 600; font-size: 12.5px; letter-spacing: 2.3px; color: var(--green); margin-top: 3px; }
  .card--front .wordmark { top: 300px; }
  .card--front .wordmark__name { color: var(--navy); }
  .card--back .wordmark { top: 232px; }
  .card--back .wordmark__name { color: var(--white); font-size: 27px; }
  .card--back .wordmark__tagline { letter-spacing: 2.1px; }
</style>
</head>
<body>

<section class="card card--front">
  <div class="brand-block">
    <span class="brand-block__square"></span>
    <span>Bayfield<br>Capital<br>Works</span>
  </div>

  <div class="divider"></div>

  <div class="person">
    <h1 class="person__name">Glen R. Harlow</h1>
    <p class="person__title">Small Business Advisor</p>
  </div>

  <ul class="contacts">
    <li>
      <svg viewBox="0 0 24 24"><path d="M2 9c0-3 5-5 10-5s10 2 10 5v2h-5V9c-2-1-8-1-10 0v2H2zM5 12h14l2 9H3z"/></svg>
      (555) 806-2147
    </li>
    <li>
      <svg viewBox="0 0 24 24"><path d="M6.6 10.8a15 15 0 0 0 6.6 6.6l2.2-2.2a1 1 0 0 1 1-.25 11.4 11.4 0 0 0 3.6.57 1 1 0 0 1 1 1V20a1 1 0 0 1-1 1A17 17 0 0 1 3 4a1 1 0 0 1 1-1h3.5a1 1 0 0 1 1 1c0 1.25.2 2.45.57 3.57a1 1 0 0 1-.25 1z"/></svg>
      (555) 274-3918
    </li>
    <li>
      <svg viewBox="0 0 24 24"><path d="M2 5h20v2l-10 6L2 7zM2 9l10 6 10-6v10H2z"/></svg>
      g.harlow@bayfieldcapitalworks.example
    </li>
    <li>
      <svg viewBox="0 0 24 24"><circle cx="12" cy="12" r="10"/></svg>
      www.bayfieldcapitalworks.example
    </li>
  </ul>

  <div class="wordmark">
    <p class="wordmark__name">BAYFIELD CAPITAL WORKS, INC</p>
    <p class="wordmark__tagline">TRUSTED GUIDANCE TO BUY OR SELL YOUR BUSINESS</p>
  </div>
</section>

<section class="card card--back">
  <div class="brand-block">
    <span class="brand-block__square"></span>
    <span>Bayfield Capital Works</span>
  </div>
  <div class="wordmark">
    <p class="wordmark__name">BAYFIELD CAPITAL WORKS, INC</p>
    <p class="wordmark__tagline">TRUSTED GUIDANCE TO BUY OR SELL YOUR BUSINESS</p>
  </div>
</section>

</body>
</html>
```